Kestrelford Therapy and Consulting

Build & publish a WordPress website that advertises and markets my private practice - which is delivering, and consulting in, psychological therapies. I also need to be able to edit content (eg text and images) on the end product thereafter. It should have a call to action on the homepage, links to:
• About me
• For referrers (with link to service fees)
• Contact details – phone#, email address, location, operating hours, and service fees
• Other resources

Target Market(s)

People struggling with mental health, relationships, and/or psychological disorders

Industry/Entity Type

Mental health

Coding

Coded - Design and coding required

Number of Pages Required

4 page

Requirements
Must have
• WordPress
Nice to have
• Please make my logo standout on the home page
Should not have
• No testimonials - they're forbidden for psychologists in Australia

```html
<!DOCTYPE html>
<html lang="en">
<head>
<meta charset="utf-8">
<title>Kestrelford Therapy and Consulting – Home</title>
<link href="https://fonts.googleapis.com/css2?family=Lora:wght@400;600&family=Roboto:wght@400;500;700&display=swap" rel="stylesheet">
<style>
:root{
  --stage:#c9c9c9;
  --white:#ffffff;
  --ink:#1d1d1f;
  --muted:#6f6f76;
  --purple:#b57fd8;
  --cyan:#5cc6e0;
  --soft:#f3f3f5;
  --line:#e4e4ea;
  --black:#0c0c0d;
  --grad:linear-gradient(135deg,var(--purple),var(--cyan));
  --btn:linear-gradient(90deg,var(--cyan),var(--purple));
}
*{box-sizing:border-box;margin:0;padding:0}
html,body{width:1200px;height:2558px;overflow:hidden;background:var(--stage);font-family:"Roboto",Arial,sans-serif;color:var(--ink)}
.page{position:absolute;top:65px;width:499px;height:2445px;background:var(--white);overflow:hidden}
.page--a{left:72px}.page--b{left:637px}
.abs{position:absolute}
.serif{font-family:"Lora",Georgia,serif}
.small{font-size:4.6px;line-height:8.4px;color:var(--muted)}
.btn{position:absolute;height:17px;border-radius:9px;background:var(--btn);color:#fff;font-size:5.3px;font-weight:500;display:flex;align-items:center;justify-content:center;letter-spacing:.3px}
.btn--light{background:#fff;color:var(--purple)}

/* photo fills: soft tonal gradients standing in for photography */
.ph-hero-a{background:
  radial-gradient(ellipse 22% 40% at 62% 62%,#7d8794 0,rgba(125,135,148,0) 100%),
  radial-gradient(ellipse 18% 45% at 86% 48%,#f4f1ec 0,rgba(244,241,236,0) 100%),
  radial-gradient(ellipse 14% 30% at 92% 20%,#3a2e28 0,rgba(58,46,40,0) 100%),
  linear-gradient(100deg,#f6f7f9 0,#eceef1 45%,#c4cad2 70%,#9aa3ae 100%)}
.ph-hero-b{background:
  radial-gradient(ellipse 20% 40% at 63% 45%,#b89a6e 0,rgba(184,154,110,0) 100%),
  radial-gradient(ellipse 20% 45% at 88% 62%,#f0a58f 0,rgba(240,165,143,0) 100%),
  radial-gradient(ellipse 30% 50% at 55% 85%,#4a2c22 0,rgba(74,44,34,0) 100%),
  linear-gradient(100deg,#f6f7f9 0,#eceef1 40%,#c9c2b8 70%,#8e7c6c 100%)}
.ph-portrait{background:
  radial-gradient(ellipse 60% 45% at 50% 100%,#35587f 0,rgba(53,88,127,0) 100%),
  radial-gradient(circle at 50% 40%,#b7a9a0 0,#8f98a3 45%,#4d6178 80%)}
.ph-tile-1{background:linear-gradient(180deg,rgba(0,0,0,0) 45%,rgba(20,20,22,.85)),radial-gradient(ellipse at 30% 40%,#c8a38a,transparent 60%),linear-gradient(135deg,#6f7d6a,#2e3a33)}
.ph-tile-2{background:linear-gradient(180deg,rgba(0,0,0,0) 45%,rgba(20,20,22,.85)),radial-gradient(ellipse at 70% 30%,#f2f1ec,transparent 55%),linear-gradient(135deg,#b9bfc2,#4b4f55)}
.ph-tile-4{background:linear-gradient(180deg,rgba(0,0,0,0) 45%,rgba(20,20,22,.85)),radial-gradient(ellipse at 75% 35%,#e9e6e2,transparent 55%),linear-gradient(135deg,#7d6a5c,#393432)}
.ph-mod-1{background:radial-gradient(ellipse at 50% 40%,#5a636e,transparent 60%),linear-gradient(180deg,#dfe4e8,#9aa5af)}
.ph-mod-2{background:radial-gradient(ellipse at 25% 45%,#d98a5c,transparent 45%),radial-gradient(ellipse at 75% 50%,#2b2b2e,transparent 45%),linear-gradient(180deg,#f3f3f1,#cfd3d6)}
.ph-mod-3{background:radial-gradient(ellipse at 35% 50%,#6b4b35,transparent 55%),radial-gradient(ellipse at 75% 50%,#c9b39a,transparent 45%),linear-gradient(180deg,#4a3a2f,#241c17)}
.ph-quality{background:radial-gradient(ellipse at 30% 50%,#7f9bbd,transparent 45%),radial-gradient(ellipse at 75% 55%,#c9c3ba,transparent 45%),linear-gradient(180deg,#e4ddd1,#b8ab96)}
.ph-background{background:radial-gradient(ellipse at 30% 40%,#c98f7a,transparent 40%),radial-gradient(ellipse at 70% 75%,#1f5f78,transparent 50%),radial-gradient(ellipse at 85% 90%,#c9a27a,transparent 40%),linear-gradient(135deg,#2f6b7e,#6f8c8f)}
.ph-map{background:
  radial-gradient(circle at 25% 30%,#b8b4a8 0,transparent 18%),
  radial-gradient(circle at 70% 60%,#a9a597 0,transparent 22%),
  radial-gradient(circle at 45% 80%,#6c7a63 0,transparent 20%),
  linear-gradient(135deg,#8c8f86,#5d6861)}

/* nav */
.nav{left:0;top:0;width:499px;height:32px;background:#fff}
.brand{left:60px;top:9px;display:flex;align-items:center;gap:4px;font-family:"Lora",Georgia,serif;font-size:9px;color:#5a5a66}
.brand i{width:13px;height:13px;border-radius:50%;background:#e2e8f1;display:block}
.menu{left:185px;top:13px;display:flex;gap:14px;font-size:5.5px;font-weight:500}
.menu span:first-child{border-bottom:1px solid var(--purple);padding-bottom:2px}
.call{left:377px;top:8px;display:flex;gap:5px;align-items:center}
.call i{width:15px;height:15px;border-radius:50%;background:var(--grad);display:block}
.call small{display:block;font-size:4px;color:var(--muted);line-height:5px}
.call b{display:block;font-size:6px;line-height:8px}

/* hero */
.hero-photo{left:0;top:32px;width:499px;height:270px}
.hero-title{left:60px;top:96px;font-size:15px;font-weight:600}
.hero-text{left:60px;top:121px;font-size:5.5px;line-height:10px;font-weight:500}
.slide-rail{left:20px;top:104px;width:10px;height:110px}
.hero-curve{left:0;top:230px}

/* profile */
.portrait{left:62px;top:298px;width:166px;height:166px;border-radius:50%;border:2px solid var(--purple)}
.profile-name{left:262px;top:309px;font-size:12px;font-weight:600}
.profile-name small{font-size:5px;font-weight:400}
.profile-role{left:262px;top:330px;font-size:5.5px;font-weight:500}
.profile-text{left:262px;top:344px;width:177px;text-align:justify}

/* sections */
.h2{position:absolute;left:0;width:499px;text-align:center;font-family:"Lora",Georgia,serif;font-size:12px;font-weight:600}
.sub{position:absolute;left:0;width:499px;text-align:center}
.svc{top:540px;width:121px;height:136px;display:flex;align-items:flex-end;justify-content:center;padding-bottom:10px;color:#fff;font-size:6.5px;font-weight:600}
.svc--active{background:linear-gradient(135deg,#b38ee0,#7fc6e6);flex-direction:column;justify-content:flex-start;align-items:center;padding:42px 14px 0;text-align:center}
.svc--active b{font-size:6.5px;font-weight:500}
.svc--active p{font-size:4.4px;line-height:8px;margin-top:5px;text-align:justify;font-weight:400}
.area{width:117px;height:129px;border:1px solid var(--line);border-radius:10px;box-shadow:0 2px 6px rgba(0,0,0,.06);text-align:center;padding-top:12px}
.area i{display:block;width:36px;height:36px;border-radius:50%;background:var(--grad);margin:0 auto 12px}
.area h4{font-size:6px;font-weight:700}
.area p{font-size:4.4px;line-height:8.6px;color:var(--muted);padding:2px 8px}
.area a{font-size:4.4px;color:var(--cyan);font-weight:700}
.band{left:0;width:499px;height:106px;background:linear-gradient(90deg,#b385d9,#87b0e3 55%,#64c3df);color:#fff;text-align:center}
.band h3{font-family:"Lora",Georgia,serif;font-size:12px;font-weight:600;margin-top:18px}
.band p{font-size:5px;line-height:9px;margin:6px auto 0;width:340px}
.mod{width:117px;height:116px;background:#fff;box-shadow:0 2px 6px rgba(0,0,0,.12);text-align:center;padding:3px}
.mod .ph{height:82px}
.mod i{display:block;width:24px;height:24px;border-radius:50%;background:var(--grad);border:2px solid #fff;margin:-14px auto 2px}
.mod b{font-size:6px}
.arrow{font-size:16px;color:#444}
.field{position:absolute;left:60px;width:179px;height:17px;border:1px solid var(--line);background:#fff;font-size:4.4px;color:var(--muted);padding:6px 8px}
.footer{left:0;width:499px;background:var(--black);color:#fff}
.fcol{font-size:4.4px;line-height:10px;color:#ddd}
.fcol b{font-size:4.8px;color:#fff;display:block;margin-bottom:2px}
</style>
</head>
<body>

<!-- Layout A -->
<section class="page page--a">
  <div class="hero-photo ph-hero-a abs" role="img" aria-label="Photo of an older man reading with a clinician beside him"></div>
  <header class="nav abs">
    <div class="brand abs"><i></i>Kestrelford</div>
    <nav class="menu abs"><span>Home</span><span>About Me</span><span>Services</span><span>Resources</span><span>Contact</span></nav>
    <div class="call abs"><i></i><div><small>Call Us Now</small><b>0400 555 019</b></div></div>
  </header>
  <svg class="slide-rail abs" viewBox="0 0 10 110"><circle cx="5" cy="26" r="6" fill="#111"/><path d="M4 23l3 3-3 3z" fill="#fff"/><line x1="5" y1="34" x2="5" y2="70" stroke="#999" stroke-width=".5"/><circle cx="5" cy="74" r="2.5" fill="none" stroke="#999" stroke-width=".5"/></svg>
  <h1 class="hero-title abs serif">Welcome To Kestrelford</h1>
  <p class="hero-text abs">Currently I am available between 9am to 5pm<br>on Wednesdays only.</p>
  <div class="btn" style="left:60px;top:149px;width:76px">GET STARTED ⟶</div>
  <svg class="hero-curve abs" width="499" height="80" viewBox="0 0 499 80"><defs><linearGradient id="ga" x1="0" x2="1"><stop offset="0" stop-color="#5cc6e0"/><stop offset="1" stop-color="#b57fd8"/></linearGradient></defs><path d="M0 70Q250 -10 499 60V80H0Z" fill="#fff"/><path d="M0 70Q250 -10 499 60" fill="none" stroke="url(#ga)" stroke-width="3"/></svg>

  <div class="portrait ph-portrait abs" role="img" aria-label="Portrait photo of the psychologist"></div>
  <h2 class="profile-name abs serif">Mr. Daniel Marsh <small>BAppSc(Hons), MPsych(Clin)</small></h2>
  <p class="profile-role abs">Clinical Psychologist, Clinical Supervisor</p>
  <div class="profile-text abs small"><p>I'm a clinical psychologist, psychotherapist, EMDR Consultant, and Resource Therapy Practitioner and Trainer.</p><p style="margin-top:3px">My main interest in therapy is helping people overcome the inner obstacles that cause them emotional pain and suffering, and that maintain behavioural patterns that are damaging or self-defeating.</p><p style="margin-top:3px">I also like to train, coach and mentor other therapists in effective therapies.</p></div>
  <div class="btn" style="left:262px;top:433px;width:68px">READ MORE ⟶</div>

  <h2 class="h2" style="top:491px">Our Services</h2>
  <p class="sub small" style="top:513px">I provide trauma-focused psychotherapy to clients and consult with other mental health clinicians on their practice of psychotherapy.</p>
  <div class="svc ph-tile-1 abs" style="left:0" role="img" aria-label="Photo of a therapy session">Psychotherapy</div>
  <div class="svc ph-tile-2 abs" style="left:126px" role="img" aria-label="Photo of an assessment meeting">Assessment</div>
  <div class="svc svc--active abs" style="left:253px"><b>Clinical Supervision</b><p>Lorem ipsum dolor sit amet, consectetur adipiscing elit, sed do eiusmod tempor incididunt ut labore et dolore magna aliqua. Ut enim ad minim veniam, quis nostrud exercitation ullamco laboris nisi ut aliquip.</p></div>
  <div class="svc ph-tile-4 abs" style="left:380px" role="img" aria-label="Photo of a clinician in training">Professional Training</div>

  <h2 class="h2" style="top:708px">Areas Of Special Interest</h2>
  <div class="area abs" style="left:60px;top:741px"><i></i><h4>ADDICTION</h4><p>Sed ut perspiciatis unde omnis iste natus error sit voluptatem accusantium enim doloremque laudantium,</p><a>READ MORE ➜</a></div>
  <div class="area abs" style="left:191px;top:741px"><i></i><h4>ANXIETY</h4><p>Sed ut perspiciatis unde omnis iste natus error sit voluptatem accusantium enim doloremque laudantium,</p><a>READ MORE ➜</a></div>
  <div class="area abs" style="left:322px;top:741px"><i></i><h4>DEPRESSION</h4><p>Sed ut perspiciatis unde omnis iste natus error sit voluptatem accusantium enim doloremque laudantium,</p><a>READ MORE ➜</a></div>
  <div class="area abs" style="left:60px;top:881px"><i></i><h4>PHOBIAS</h4><p>Sed ut perspiciatis unde omnis iste natus error sit voluptatem accusantium enim doloremque laudantium,</p><a>READ MORE ➜</a></div>
  <div class="area abs" style="left:191px;top:881px"><i></i><h4>RELATIONSHIP ISSUES</h4><p>Sed ut perspiciatis unde omnis iste natus error sit voluptatem accusantium enim doloremque laudantium,</p><a>READ MORE ➜</a></div>
  <div class="area abs" style="left:322px;top:881px"><i></i><h4>SELF DEVELOPMENT</h4><p>Sed ut perspiciatis unde omnis iste natus error sit voluptatem accusantium enim doloremque laudantium,</p><a>READ MORE ➜</a></div>
  <svg class="abs" style="left:240px;top:1020px" width="20" height="5"><circle cx="2" cy="2.5" r="1.5" fill="#ddd"/><circle cx="9" cy="2.5" r="1.5" fill="#b57fd8"/><circle cx="16" cy="2.5" r="1.5" fill="#ddd"/></svg>

  <div class="band abs" style="top:1061px"><h3>Fees</h3><p>My standard fee for a 50 to 60 minute psychological therapy session is $220. For those who are on low or no income my concession fee is $180. Medicare currently rebates 137.05 for a 50+ minute psychological therapy session if a MHCP is in place.</p></div>
  <div class="btn btn--light" style="left:215px;top:1128px;width:70px">PAY NOW ⟶</div>

  <h2 class="h2" style="top:1198px">Modalities / Approach</h2>
  <div class="arrow abs" style="left:33px;top:1274px">‹</div><div class="arrow abs" style="left:456px;top:1274px">›</div>
  <div class="mod abs" style="left:60px;top:1229px"><div class="ph ph-mod-1" role="img" aria-label="Photo of a distressed man"></div><i></i><b>Existential</b></div>
  <div class="mod abs" style="left:190px;top:1236px"><div class="ph ph-mod-2" role="img" aria-label="Photo of two women talking"></div><i></i><b>Integrative</b></div>
  <div class="mod abs" style="left:322px;top:1229px"><div class="ph ph-mod-3" role="img" aria-label="Photo of a couple in a session"></div><i></i><b>Psychodynamic</b></div>
  <p class="sub small" style="top:1369px;padding:0 60px">I believe that using Eye Movement Desensitizing and Reprocessing (EMDR) therapy and Resource Therapy (RT) together addresses almost all mental illness that doesn't involve an organic component. EMDR principally addresses disturbing memories from the past that negatively impact a person in the present.</p>
  <p class="sub small" style="top:1403px;padding:0 60px">RT addresses resource states (also known as states of mind, parts, ego states, and schema modes) that are putting a person 'out of balance', i.e. they are yielding unwanted emotions or unwanted behaviours that are impairing a person's ability to function.</p>

  <svg class="abs" style="left:48px;top:1442px" width="62" height="60"><g fill="#b57fd8"><circle cx="2" cy="2" r="1"/><circle cx="8" cy="2" r="1"/><circle cx="14" cy="2" r="1"/><circle cx="20" cy="2" r="1"/><circle cx="26" cy="2" r="1"/><circle cx="32" cy="2" r="1"/><circle cx="38" cy="2" r="1"/><circle cx="44" cy="2" r="1"/><circle cx="50" cy="2" r="1"/><circle cx="56" cy="2" r="1"/><circle cx="2" cy="8" r="1"/><circle cx="2" cy="14" r="1"/><circle cx="2" cy="20" r="1"/><circle cx="2" cy="26" r="1"/><circle cx="2" cy="32" r="1"/><circle cx="2" cy="38" r="1"/><circle cx="2" cy="44" r="1"/><circle cx="2" cy="50" r="1"/></g></svg>
  <div class="ph-quality abs" style="left:60px;top:1455px;width:190px;height:147px" role="img" aria-label="Photo of a therapist talking with an older client"></div>
  <h2 class="abs serif" style="left:287px;top:1469px;font-size:12px;font-weight:600">Quality Provision</h2>
  <div class="abs small" style="left:287px;top:1490px;width:152px;text-align:justify"><p>I generally start sessions checking with how clients are feeling and coping between sessions, ascertaining whether or not the client believes we are 'on track' according to what was agreed in the treatment plan we co-created.</p><p style="margin-top:3px">I endeavour to maximise the benefit we can obtain from the number of sessions available to us.</p></div>
  <div class="btn" style="left:287px;top:1566px;width:68px">READ MORE ⟶</div>

  <div class="band abs" style="top:1635px"><h3>Transport And Parking</h3><p>There is limited paid parking in Elm Street and surrounds but, being adjacent to the GPO, Harbour House is very close to public transport.</p></div>
  <div class="btn btn--light" style="left:215px;top:1703px;width:70px">READ MORE ⟶</div>

  <div class="ph-background abs" style="left:229px;top:1773px;width:210px;height:160px" role="img" aria-label="Photo of two women in a counselling session"></div>
  <div class="abs" style="left:60px;top:1786px;width:190px;height:134px;background:#fff;box-shadow:0 2px 8px rgba(0,0,0,.08);padding:22px 17px">
    <h2 class="serif" style="font-size:12px;font-weight:400">Background</h2>
    <p class="small" style="margin-top:7px">When I first started to practice, I felt ill-prepared for the vast range of maladies of the human condition, especially as I was immersed in a setting that had so many suffering from the impact of trauma in childhood.</p>
  </div>
  <div class="btn" style="left:77px;top:1883px;width:68px">READ MORE ⟶</div>

  <div class="abs" style="left:0;top:1968px;width:499px;height:310px;background:var(--soft)"></div>
  <h2 class="h2" style="top:1992px">Contact Us</h2>
  <svg class="abs" style="left:78px;top:2034px" width="20" height="20"><path d="M10 2a6 6 0 0 0-6 6c0 5 6 10 6 10s6-5 6-10a6 6 0 0 0-6-6z" fill="none" stroke="#8fa0e0" stroke-width="1"/><circle cx="10" cy="8" r="2" fill="none" stroke="#8fa0e0"/></svg>
  <div class="abs small" style="left:106px;top:2035px;line-height:7px"><b style="color:var(--ink)">LOCATION:</b><br>Suite 4, Harbour House, 12 Elm<br>Street, Kestrelford, TAS 7000</div>
  <svg class="abs" style="left:232px;top:2034px" width="18" height="18"><path d="M4 2l4 1 1 4-2 2a10 10 0 0 0 4 4l2-2 4 1 1 4c-8 1-15-6-14-14z" fill="none" stroke="#8fa0e0" stroke-width="1"/></svg>
  <div class="abs small" style="left:258px;top:2039px;line-height:7px"><b style="color:var(--ink)">PHONE:</b><br>0400 555 019</div>
  <svg class="abs" style="left:335px;top:2038px" width="20" height="14"><rect x="1" y="1" width="18" height="12" fill="none" stroke="#c07fd8"/><path d="M1 1l9 7 9-7" fill="none" stroke="#c07fd8"/></svg>
  <div class="abs small" style="left:363px;top:2039px;line-height:7px"><b style="color:var(--ink)">EMAIL:</b><br>info@danielmarshtherapy.com</div>
  <h3 class="abs" style="left:60px;top:2075px;font-size:7px;font-weight:700">APPOINTMENTS</h3>
  <p class="abs small" style="left:60px;top:2086px">Currently I am available between 9am to 5pm on Wednesdays only.</p>
  <div class="field" style="top:2108px">First Name</div>
  <div class="field" style="top:2132px">Phone Number</div>
  <div class="field" style="top:2156px">Email Address</div>
  <div class="field" style="top:2179px;height:35px">Message</div>
  <div class="btn" style="left:60px;top:2226px;width:179px;height:15px;border-radius:0">SUBMIT</div>
  <div class="ph-map abs" style="left:265px;top:2073px;width:173px;height:172px;border:3px solid #fff;box-shadow:0 2px 6px rgba(0,0,0,.1)" role="img" aria-label="Satellite map of the practice location"></div>

  <svg class="abs" style="left:0;top:2255px" width="499" height="50" viewBox="0 0 499 50"><defs><linearGradient id="gb" x1="0" x2="1"><stop offset="0" stop-color="#5cc6e0"/><stop offset="1" stop-color="#b57fd8"/></linearGradient></defs><path d="M0 12Q250 70 499 8V50H0Z" fill="#0c0c0d"/><path d="M0 12Q250 70 499 8" fill="none" stroke="url(#gb)" stroke-width="3"/></svg>
  <footer class="footer abs" style="top:2295px;height:150px">
    <div class="abs" style="left:60px;top:64px;display:flex;align-items:center;gap:4px;font-family:Lora,Georgia,serif;font-size:9px;color:#fff"><i style="width:13px;height:13px;border-radius:50%;background:#5a6070;display:block"></i>Kestrelford</div>
    <svg class="abs" style="left:74px;top:85px" width="46" height="6"><g fill="#fff"><circle cx="3" cy="3" r="2.5"/><circle cx="15" cy="3" r="2.5"/><circle cx="27" cy="3" r="2.5"/><circle cx="39" cy="3" r="2.5"/></g></svg>
    <div class="fcol abs" style="left:167px;top:48px"><b>COMPANY</b>Home<br>About Me<br>Services<br>Resources<br>Contact</div>
    <div class="fcol abs" style="left:233px;top:48px"><b>INFORMATION</b>Privacy Policy<br>Terms of Use<br>Contact</div>
    <div class="fcol abs" style="left:315px;top:48px;width:125px;line-height:7px"><b>SUBSCRIBE TO OUR NEWSLETTER</b>Subscribe to our mailing list to receives daily updates direct to your inbox!</div>
    <div class="abs" style="left:315px;top:84px;width:124px;height:16px;border-radius:8px;background:#fff;font-size:4.4px;color:#888;padding:6px 8px">Email Address</div>
    <div class="btn" style="left:392px;top:84px;width:47px;height:16px">SUBSCRIBE</div>
    <p class="abs" style="left:0;top:133px;width:499px;text-align:center;font-size:4.6px;color:#ddd">Copy Rights © Kestrelford 2024 | Allrights Reserved</p>
  </footer>
</section>

<!-- Layout B -->
<section class="page page--b">
  <div class="hero-photo ph-hero-b abs" role="img" aria-label="Photo of two women talking in a counselling session"></div>
  <header class="nav abs">
    <div class="brand abs"><i></i>Kestrelford</div>
    <nav class="menu abs"><span>Home</span><span>About Me</span><span>Services</span><span>Resources</span><span>Contact</span></nav>
    <div class="call abs"><i></i><div><small>Call Us Now</small><b>0400 555 019</b></div></div>
  </header>
  <svg class="slide-rail abs" viewBox="0 0 10 110"><circle cx="5" cy="26" r="6" fill="#111"/><path d="M4 23l3 3-3 3z" fill="#fff"/><line x1="5" y1="34" x2="5" y2="70" stroke="#999" stroke-width=".5"/><circle cx="5" cy="74" r="2.5" fill="none" stroke="#999" stroke-width=".5"/></svg>
  <h1 class="hero-title abs serif">Welcome To Kestrelford</h1>
  <p class="hero-text abs">Currently I am available between 9am to 5pm<br>on Wednesdays only.</p>
  <div class="btn" style="left:60px;top:149px;width:76px">GET STARTED ⟶</div>
  <svg class="hero-curve abs" width="499" height="80" viewBox="0 0 499 80"><defs><linearGradient id="gc" x1="0" x2="1"><stop offset="0" stop-color="#5cc6e0"/><stop offset="1" stop-color="#b57fd8"/></linearGradient></defs><path d="M0 70Q250 -10 499 60V80H0Z" fill="#fff"/><path d="M0 70Q250 -10 499 60" fill="none" stroke="url(#gc)" stroke-width="3"/></svg>

  <div class="portrait ph-portrait abs" role="img" aria-label="Portrait photo of the psychologist"></div>
  <h2 class="profile-name abs serif">Mr. Daniel Marsh <small>BAppSc(Hons), MPsych(Clin)</small></h2>
  <p class="profile-role abs">Clinical Psychologist, Clinical Supervisor</p>
  <div class="profile-text abs small"><p>I'm a clinical psychologist, psychotherapist, EMDR Consultant, and Resource Therapy Practitioner and Trainer.</p><p style="margin-top:3px">My main interest in therapy is helping people overcome the inner obstacles that cause them emotional pain and suffering, and that maintain behavioural patterns that are damaging or self-defeating.</p><p style="margin-top:3px">I also like to train, coach and mentor other therapists in effective therapies.</p></div>
  <div class="btn" style="left:262px;top:433px;width:68px">READ MORE ⟶</div>

  <h2 class="h2" style="top:491px">Our Services</h2>
  <p class="sub small" style="top:513px">I provide trauma-focused psychotherapy to clients and consult with other mental health clinicians on their practice of psychotherapy.</p>
  <div class="svc ph-tile-1 abs" style="left:0" role="img" aria-label="Photo of a therapy session">Psychotherapy</div>
  <div class="svc ph-tile-2 abs" style="left:126px" role="img" aria-label="Photo of an assessment meeting">Assessment</div>
  <div class="svc svc--active abs" style="left:253px"><b>Clinical Supervision</b><p>Lorem ipsum dolor sit amet, consectetur adipiscing elit, sed do eiusmod tempor incididunt ut labore et dolore magna aliqua. Ut enim ad minim veniam, quis nostrud exercitation ullamco laboris nisi ut aliquip.</p></div>
  <div class="svc ph-tile-4 abs" style="left:380px" role="img" aria-label="Photo of a clinician in training">Professional Training</div>

  <h2 class="h2" style="top:708px">Areas Of Special Interest</h2>
  <div class="area abs" style="left:60px;top:741px"><i></i><h4>ADDICTION</h4><p>Sed ut perspiciatis unde omnis iste natus error sit voluptatem accusantium enim doloremque laudantium,</p><a>READ MORE ➜</a></div>
  <div class="area abs" style="left:191px;top:741px"><i></i><h4>ANXIETY</h4><p>Sed ut perspiciatis unde omnis iste natus error sit voluptatem accusantium enim doloremque laudantium,</p><a>READ MORE ➜</a></div>
  <div class="area abs" style="left:322px;top:741px"><i></i><h4>DEPRESSION</h4><p>Sed ut perspiciatis unde omnis iste natus error sit voluptatem accusantium enim doloremque laudantium,</p><a>READ MORE ➜</a></div>
  <div class="area abs" style="left:60px;top:881px"><i></i><h4>PHOBIAS</h4><p>Sed ut perspiciatis unde omnis iste natus error sit voluptatem accusantium enim doloremque laudantium,</p><a>READ MORE ➜</a></div>
  <div class="area abs" style="left:191px;top:881px"><i></i><h4>RELATIONSHIP ISSUES</h4><p>Sed ut perspiciatis unde omnis iste natus error sit voluptatem accusantium enim doloremque laudantium,</p><a>READ MORE ➜</a></div>
  <div class="area abs" style="left:322px;top:881px"><i></i><h4>SELF DEVELOPMENT</h4><p>Sed ut perspiciatis unde omnis iste natus error sit voluptatem accusantium enim doloremque laudantium,</p><a>READ MORE ➜</a></div>
  <svg class="abs" style="left:240px;top:1020px" width="20" height="5"><circle cx="2" cy="2.5" r="1.5" fill="#ddd"/><circle cx="9" cy="2.5" r="1.5" fill="#b57fd8"/><circle cx="16" cy="2.5" r="1.5" fill="#ddd"/></svg>

  <div class="band abs" style="top:1061px"><h3>Fees</h3><p>My standard fee for a 50 to 60 minute psychological therapy session is $220. For those who are on low or no income my concession fee is $180. Medicare currently rebates 137.05 for a 50+ minute psychological therapy session if a MHCP is in place.</p></div>
  <div class="btn btn--light" style="left:215px;top:1128px;width:70px">PAY NOW ⟶</div>

  <h2 class="h2" style="top:1198px">Modalities / Approach</h2>
  <div class="arrow abs" style="left:33px;top:1274px">‹</div><div class="arrow abs" style="left:456px;top:1274px">›</div>
  <div class="mod abs" style="left:60px;top:1229px"><div class="ph ph-mod-1" role="img" aria-label="Photo of a distressed man"></div><i></i><b>Existential</b></div>
  <div class="mod abs" style="left:190px;top:1236px"><div class="ph ph-mod-2" role="img" aria-label="Photo of two women talking"></div><i></i><b>Integrative</b></div>
  <div class="mod abs" style="left:322px;top:1229px"><div class="ph ph-mod-3" role="img" aria-label="Photo of a couple in a session"></div><i></i><b>Psychodynamic</b></div>
  <p class="sub small" style="top:1369px;padding:0 60px">I believe that using Eye Movement Desensitizing and Reprocessing (EMDR) therapy and Resource Therapy (RT) together addresses almost all mental illness that doesn't involve an organic component. EMDR principally addresses disturbing memories from the past that negatively impact a person in the present.</p>
  <p class="sub small" style="top:1403px;padding:0 60px">RT addresses resource states (also known as states of mind, parts, ego states, and schema modes) that are putting a person 'out of balance', i.e. they are yielding unwanted emotions or unwanted behaviours that are impairing a person's ability to function.</p>

  <svg class="abs" style="left:48px;top:1442px" width="62" height="60"><g fill="#b57fd8"><circle cx="2" cy="2" r="1"/><circle cx="8" cy="2" r="1"/><circle cx="14" cy="2" r="1"/><circle cx="20" cy="2" r="1"/><circle cx="26" cy="2" r="1"/><circle cx="32" cy="2" r="1"/><circle cx="38" cy="2" r="1"/><circle cx="44" cy="2" r="1"/><circle cx="50" cy="2" r="1"/><circle cx="56" cy="2" r="1"/><circle cx="2" cy="8" r="1"/><circle cx="2" cy="14" r="1"/><circle cx="2" cy="20" r="1"/><circle cx="2" cy="26" r="1"/><circle cx="2" cy="32" r="1"/><circle cx="2" cy="38" r="1"/><circle cx="2" cy="44" r="1"/><circle cx="2" cy="50" r="1"/></g></svg>
  <div class="ph-quality abs" style="left:60px;top:1455px;width:190px;height:147px" role="img" aria-label="Photo of a therapist talking with an older client"></div>
  <h2 class="abs serif" style="left:287px;top:1469px;font-size:12px;font-weight:600">Quality Provision</h2>
  <div class="abs small" style="left:287px;top:1490px;width:152px;text-align:justify"><p>I generally start sessions checking with how clients are feeling and coping between sessions, ascertaining whether or not the client believes we are 'on track' according to what was agreed in the treatment plan we co-created.</p><p style="margin-top:3px">I endeavour to maximise the benefit we can obtain from the number of sessions available to us.</p></div>
  <div class="btn" style="left:287px;top:1566px;width:68px">READ MORE ⟶</div>

  <div class="band abs" style="top:1635px"><h3>Transport And Parking</h3><p>There is limited paid parking in Elm Street and surrounds but, being adjacent to the GPO, Harbour House is very close to public transport.</p></div>
  <div class="btn btn--light" style="left:215px;top:1703px;width:70px">READ MORE ⟶</div>

  <div class="ph-background abs" style="left:229px;top:1773px;width:210px;height:160px" role="img" aria-label="Photo of two women in a counselling session"></div>
  <div class="abs" style="left:60px;top:1786px;width:190px;height:134px;background:#fff;box-shadow:0 2px 8px rgba(0,0,0,.08);padding:22px 17px">
    <h2 class="serif" style="font-size:12px;font-weight:400">Background</h2>
    <p class="small" style="margin-top:7px">When I first started to practice, I felt ill-prepared for the vast range of maladies of the human condition, especially as I was immersed in a setting that had so many suffering from the impact of trauma in childhood.</p>
  </div>
  <div class="btn" style="left:77px;top:1883px;width:68px">READ MORE ⟶</div>

  <div class="abs" style="left:0;top:1968px;width:499px;height:310px;background:var(--soft)"></div>
  <h2 class="h2" style="top:1992px">Contact Us</h2>
  <svg class="abs" style="left:78px;top:2034px" width="20" height="20"><path d="M10 2a6 6 0 0 0-6 6c0 5 6 10 6 10s6-5 6-10a6 6 0 0 0-6-6z" fill="none" stroke="#8fa0e0" stroke-width="1"/><circle cx="10" cy="8" r="2" fill="none" stroke="#8fa0e0"/></svg>
  <div class="abs small" style="left:106px;top:2035px;line-height:7px"><b style="color:var(--ink)">LOCATION:</b><br>Suite 4, Harbour House, 12 Elm<br>Street, Kestrelford, TAS 7000</div>
  <svg class="abs" style="left:232px;top:2034px" width="18" height="18"><path d="M4 2l4 1 1 4-2 2a10 10 0 0 0 4 4l2-2 4 1 1 4c-8 1-15-6-14-14z" fill="none" stroke="#8fa0e0" stroke-width="1"/></svg>
  <div class="abs small" style="left:258px;top:2039px;line-height:7px"><b style="color:var(--ink)">PHONE:</b><br>0400 555 019</div>
  <svg class="abs" style="left:335px;top:2038px" width="20" height="14"><rect x="1" y="1" width="18" height="12" fill="none" stroke="#c07fd8"/><path d="M1 1l9 7 9-7" fill="none" stroke="#c07fd8"/></svg>
  <div class="abs small" style="left:363px;top:2039px;line-height:7px"><b style="color:var(--ink)">EMAIL:</b><br>info@danielmarshtherapy.com</div>
  <h3 class="abs" style="left:60px;top:2075px;font-size:7px;font-weight:700">APPOINTMENTS</h3>
  <p class="abs small" style="left:60px;top:2086px">Currently I am available between 9am to 5pm on Wednesdays only.</p>
  <div class="field" style="top:2108px">First Name</div>
  <div class="field" style="top:2132px">Phone Number</div>
  <div class="field" style="top:2156px">Email Address</div>
  <div class="field" style="top:2179px;height:35px">Message</div>
  <div class="btn" style="left:60px;top:2226px;width:179px;height:15px;border-radius:0">SUBMIT</div>
  <div class="ph-map abs" style="left:265px;top:2073px;width:173px;height:172px;border:3px solid #fff;box-shadow:0 2px 6px rgba(0,0,0,.1)" role="img" aria-label="Satellite map of the practice location"></div>

  <svg class="abs" style="left:0;top:2255px" width="499" height="50" viewBox="0 0 499 50"><defs><linearGradient id="gd" x1="0" x2="1"><stop offset="0" stop-color="#5cc6e0"/><stop offset="1" stop-color="#b57fd8"/></linearGradient></defs><path d="M0 12Q250 70 499 8V50H0Z" fill="#0c0c0d"/><path d="M0 12Q250 70 499 8" fill="none" stroke="url(#gd)" stroke-width="3"/></svg>
  <footer class="footer abs" style="top:2295px;height:150px">
    <div class="abs" style="left:60px;top:64px;display:flex;align-items:center;gap:4px;font-family:Lora,Georgia,serif;font-size:9px;color:#fff"><i style="width:13px;height:13px;border-radius:50%;background:#5a6070;display:block"></i>Kestrelford</div>
    <svg class="abs" style="left:74px;top:85px" width="46" height="6"><g fill="#fff"><circle cx="3" cy="3" r="2.5"/><circle cx="15" cy="3" r="2.5"/><circle cx="27" cy="3" r="2.5"/><circle cx="39" cy="3" r="2.5"/></g></svg>
    <div class="fcol abs" style="left:167px;top:48px"><b>COMPANY</b>Home<br>About Me<br>Services<br>Resources<br>Contact</div>
    <div class="fcol abs" style="left:233px;top:48px"><b>INFORMATION</b>Privacy Policy<br>Terms of Use<br>Contact</div>
    <div class="fcol abs" style="left:315px;top:48px;width:125px;line-height:7px"><b>SUBSCRIBE TO OUR NEWSLETTER</b>Subscribe to our mailing list to receives daily updates direct to your inbox!</div>
    <div class="abs" style="left:315px;top:84px;width:124px;height:16px;border-radius:8px;background:#fff;font-size:4.4px;color:#888;padding:6px 8px">Email Address</div>
    <div class="btn" style="left:392px;top:84px;width:47px;height:16px">SUBSCRIBE</div>
    <p class="abs" style="left:0;top:133px;width:499px;text-align:center;font-size:4.6px;color:#ddd">Copy Rights © Kestrelford 2024 | Allrights Reserved</p>
  </footer>
</section>

</body>
</html>
```